Brantor Works Business Card

Modern and Professional Business Card for a Med size construction/development company.

See the samples below for the design I like … but I need ideas for incorporating the red company logo while still keeping the clean look of the card samples that are attached.

Logo and tag line on the back … info on the front.

Tagline: Quality Starts from the Ground Up

Target Market(s)

Med-Large General Contractors

Contact Information for Business Card

Brantor Works Limited
42 Fenwick Avenue
Mt. Pearl, NL
A1N 4R9

t: 709-555-0147
f: 709-555-0182
w: www.brantorworks-example.com

Font styles to use
Sans Serif

Colors
fbee3e

Requirements
Must have
• I like the black and yellow designs of the attached samples …. but I'm not sure how to incorporate the red Brantor Works logo into that design??
Nice to have
• Construction safety strips

```html
<!DOCTYPE html>
<html lang="en">
<head>
<meta charset="utf-8">
<title>Brantor Works Limited – Business Card</title>
<link rel="stylesheet" href="https://fonts.googleapis.com/css2?family=Arvo:wght@400;700&display=swap">
<style>
  :root {
    --yellow: #f9ec41;
    --black: #0c0c0c;
    --red: #e3211f;
    --white: #ffffff;
    --backdrop: #ececec;
  }
  * { margin: 0; padding: 0; box-sizing: border-box; }
  html, body {
    width: 1200px; height: 923px; overflow: hidden;
    background: var(--backdrop);
    font-family: "Arvo", serif;
  }
  .canvas { position: relative; width: 1200px; height: 923px; }
  .card {
    position: absolute; left: 290px; width: 621px; height: 355px; overflow: hidden;
  }
  /* Logo side */
  .card--logo { top: 83px; background: var(--yellow); }
  .card--logo .brand-name {
    position: absolute; left: 0; right: 0; top: 150px;
    text-align: center; color: var(--red);
    font-weight: 700; font-size: 38px; line-height: 48px; letter-spacing: 1px;
  }
  .tagline-band {
    position: absolute; left: 0; right: 0; bottom: 0; height: 55px;
    background: var(--black);
    display: flex; align-items: center; justify-content: center;
  }
  .tagline {
    color: var(--yellow); font-size: 16px; letter-spacing: 0.2px;
    text-transform: uppercase;
  }
  /* Contact side */
  .card--info { top: 485px; background: var(--black); color: var(--white); }
  .card--info .brand-name {
    position: absolute; right: 32px; top: 32px;
    text-align: right; color: var(--red);
    font-weight: 700; font-size: 25px; line-height: 32px; letter-spacing: 1px;
  }
  .person { position: absolute; left: 31px; top: 114px; display: flex; gap: 12px; }
  .person__bar { width: 20px; height: 59px; background: var(--yellow); border-radius: 5px; }
  .person__name { color: var(--yellow); font-size: 25px; line-height: 30px; margin-top: 3px; }
  .person__role { font-size: 15px; line-height: 18px; }
  .contact {
    position: absolute; right: 69px; top: 180px;
    text-align: right; font-size: 17px; line-height: 27px;
  }
  .contact-icons {
    position: absolute; right: 32px; top: 173px; width: 25px; height: 87px;
    background: var(--yellow); border-radius: 6px;
    display: flex; flex-direction: column; align-items: center; justify-content: space-around;
    padding: 4px 0;
  }
  .contact-icons svg { width: 16px; height: 16px; }
  .address {
    position: absolute; right: 69px; top: 279px;
    text-align: right; font-size: 17px; line-height: 27px;
  }
  .address-pin { position: absolute; right: 37px; top: 285px; width: 16px; height: 20px; }
</style>
</head>
<body>
<main class="canvas">
  <section class="card card--logo" aria-label="Business card, logo side">
    <p class="brand-name">BRANTOR WORKS LIMITED</p>
    <div class="tagline-band"><p class="tagline">Quality Starts from the Ground Up</p></div>
  </section>

  <section class="card card--info" aria-label="Business card, contact side">
    <p class="brand-name">BRANTOR WORKS<br>LIMITED</p>

    <div class="person">
      <span class="person__bar"></span>
      <div>
        <p class="person__name">John Doe</p>
        <p class="person__role">Contractor</p>
      </div>
    </div>

    <div class="contact">
      <p>709 - 555 - 0147</p>
      <p>709 - 555 - 0182</p>
      <p>www.brantorworks-example.com</p>
    </div>

    <div class="contact-icons">
      <svg viewBox="0 0 16 16" aria-label="Phone"><path d="M1 6 Q8 0 15 6 L13 8 L11 6.5 L11 5 Q8 4 5 5 L5 6.5 L3 8 Z M4 9 h8 l2 5 H2 Z" fill="#0c0c0c"/></svg>
      <svg viewBox="0 0 16 16" aria-label="Fax"><rect x="1" y="4" width="3" height="11" fill="#0c0c0c"/><rect x="5" y="6" width="10" height="9" fill="#0c0c0c"/><rect x="7" y="1" width="6" height="5" fill="#0c0c0c"/><rect x="7" y="8" width="6" height="1.5" fill="#f9ec41"/><rect x="7" y="11" width="6" height="1.5" fill="#f9ec41"/></svg>
      <svg viewBox="0 0 16 16" aria-label="Website"><circle cx="8" cy="8" r="6.5" fill="none" stroke="#0c0c0c" stroke-width="1.6"/><ellipse cx="8" cy="8" rx="3" ry="6.5" fill="none" stroke="#0c0c0c" stroke-width="1.2"/><line x1="1.5" y1="8" x2="14.5" y2="8" stroke="#0c0c0c" stroke-width="1.2"/></svg>
    </div>

    <div class="address">
      <p>42 Fenwick Avenue</p>
      <p>Ridgeford, NL, A0X 9Z1</p>
    </div>
    <svg class="address-pin" viewBox="0 0 16 20" aria-label="Location"><path d="M8 0 A7 7 0 0 1 15 7 C15 12 8 20 8 20 C8 20 1 12 1 7 A7 7 0 0 1 8 0 Z" fill="#f9ec41"/><circle cx="8" cy="7" r="2.6" fill="#0c0c0c"/></svg>
  </section>
</main>
</body>
</html>
```